Business Cards for new orthopaedic surgery practice

My husband and I are starting our own orthopaedic surgery practice. We are looking for a business card that is uniform, but one will have my name/title and the other will have his. You can just create one design with my name on it for now. But when I choose your design as the winning design I will ask that you add another copy with his name/title.

We are looking for classy, simple, elite all in one. We like dark blues/a little gold/yellow. Something that goes with our logo. We want our logo incorporated. Here is all the info you need:
Business name: RV Bone & Vitality Center
Location: 38517 North Willowmere Ave
Coral Springs, FL 33071
Phone: 954-218-4063
Fax: 954-582-7341
Email: info@myrvbonecare.example

Names: Lydia Vance, M.D.
Board Certified Hand and Upper Extremity Surgeon

Ebo Dansu, M.D.
Board Certified Hip & Knee Replacement/General Orthopaedic Surgeon

Can decide what you want to put on the back. Maybe a slogan:
Rooted in Care. Focused on You

I am just going to upload our logo. The only thing is if we select you as the winning design, the location, and phone numbers may change. We will need your help to update that once fully solidified.

Industry/Entity Type

Medical

Contact Information for Business Card

Colors
0054AA
0677BA
7BADD7
CADEEF
E8F1F8
0094D4
00A9DD
6FCCEA
C7EBF8
E9F6FB

Requirements
Must have
• class, appeal,
Should not have
• We want to air on the side of masculine if we are looking at masculine vs. feminine feel. But we still want it classy, sophisticated, and something we will love

```html
<!DOCTYPE html>
<html lang="en">
<head>
<meta charset="utf-8">
<title>RV Bone &amp; Vitality Center – Business Card</title>
<link rel="stylesheet" href="https://fonts.googleapis.com/css2?family=Poppins:wght@300;400;600&family=Lora:wght@500&display=swap">
<style>
  :root {
    --navy: #2a4087;
    --navy-light: #3551a0;
    --cyan: #13b3e3;
    --ink-grey: #7a7a7a;
    --paper: #ffffff;
    --backdrop: #e9edf3;
  }
  * { margin: 0; padding: 0; box-sizing: border-box; }
  html, body { width: 1200px; height: 900px; overflow: hidden; background: var(--backdrop); }

  .card {
    position: absolute; left: 250px; width: 700px; height: 400px;
    overflow: hidden; box-shadow: 0 8px 24px rgba(20, 30, 60, 0.18);
  }
  .card-front { top: 35px; background: var(--paper); }
  .card-back { top: 465px; background: var(--navy); }

  /* Front */
  .contact-band {
    position: absolute; left: 0; top: 190px; width: 427px; height: 210px;
    background: var(--navy);
  }
  .brand {
    position: absolute; display: flex; align-items: center; gap: 16px;
  }
  .card-front .brand { left: 40px; top: 48px; }
  .brand-mark { width: 18px; height: 18px; flex: none; }
  .card-front .brand-mark { background: var(--navy); }
  .brand-name {
    font-family: "Lora", serif; font-weight: 500; font-size: 25px;
    text-transform: uppercase; letter-spacing: 1px; line-height: 1.1;
  }
  .card-front .brand-name { color: var(--navy); }

  .person {
    position: absolute; right: 44px; top: 138px; text-align: right;
    font-family: "Poppins", sans-serif;
  }
  .person-name { font-weight: 600; font-size: 20px; color: var(--cyan); line-height: 1.3; }
  .person-title { font-weight: 300; font-size: 13px; color: var(--ink-grey); }
  .accent-bar {
    position: absolute; right: 0; top: 146px; width: 26px; height: 42px;
    background: var(--cyan);
  }

  .address {
    position: absolute; left: 40px; top: 218px;
    font-family: "Poppins", sans-serif; font-weight: 400; font-size: 14.5px;
    color: var(--paper); line-height: 1.5;
  }
  .contact-list { list-style: none; margin-top: 12px; }
  .contact-list li { display: flex; align-items: center; gap: 9px; }
  .contact-list svg { width: 14px; height: 14px; flex: none; }

  .tree-art {
    position: absolute; left: 400px; top: 220px; width: 200px; height: 180px;
    background: linear-gradient(160deg, var(--navy-light) 0%, var(--navy) 100%);
    border-radius: 94px 94px 0 0;
  }

  /* Back */
  .back-pattern {
    position: absolute; inset: 0;
    background: linear-gradient(135deg, #2c4490 0%, var(--navy) 50%, #273c80 100%);
  }
  .card-back .brand { left: 410px; top: 145px; gap: 18px; }
  .card-back .brand-mark { background: var(--paper); }
  .brand-divider { width: 2px; height: 96px; background: var(--paper); }
  .card-back .brand-name { color: var(--paper); font-size: 24px; }
</style>
</head>
<body>
  <section class="card card-front">
    <div class="contact-band"></div>

    <div class="brand">
      <span class="brand-mark"></span>
      <span class="brand-name">RV Bone &amp;<br>Vitality<br>Center</span>
    </div>

    <div class="person">
      <p class="person-name">Lydia Vance, M.D.</p>
      <p class="person-title">Hand and Upper Extremity Surgery</p>
    </div>
    <div class="accent-bar"></div>

    <div class="address">
      <p>38517 North Willowmere Ave<br>Coral Springs, FL 33071</p>
      <ul class="contact-list">
        <li>
          <svg viewBox="0 0 24 24"><path fill="#fff" d="M6.6 10.8a15 15 0 0 0 6.6 6.6l2.2-2.2c.3-.3.7-.4 1-.2 1.1.4 2.3.6 3.6.6.6 0 1 .4 1 1V20c0 .6-.4 1-1 1A17 17 0 0 1 3 4c0-.6.4-1 1-1h3.5c.6 0 1 .4 1 1 0 1.3.2 2.5.6 3.6.1.3 0 .7-.2 1z"/></svg>
          954-218-4063
        </li>
        <li>
          <svg viewBox="0 0 24 24"><path fill="#fff" d="M6 3h10v5H6zM4 9h16a1 1 0 0 1 1 1v8h-4v3H7v-3H3v-8a1 1 0 0 1 1-1zm5 7v3h6v-3z"/></svg>
          954-582-7341
        </li>
        <li>
          <svg viewBox="0 0 24 24"><path fill="#fff" d="M3 5h18v14H3zm2 2v.5l7 4.5 7-4.5V7z"/></svg>
          info@myrvbonecare.example
        </li>
      </ul>
    </div>

    <div class="tree-art" role="img" aria-label="Decorative leafy tree growing from a column of stacked blocks"></div>
  </section>

  <section class="card card-back">
    <div class="back-pattern" role="img" aria-label="Repeating tone-on-tone emblem pattern in lighter and darker navy"></div>
    <div class="brand">
      <span class="brand-mark"></span>
      <span class="brand-divider"></span>
      <span class="brand-name">RV Bone &amp;<br>Vitality<br>Center</span>
    </div>
  </section>
</body>
</html>
```